Design a modern, classy & professional business card for an online real estate agency, specializing in medium-luxury properties in Thailand and later in Singapore and UK.

Possible design ideas so far: (not essential)

- curved corner(s) to the card, white on front & turquoise on back or visa versa.

- front of card - clear and simple, company name in metallic grey/monochrome, logo graphic & company name on front in spot UV or embossed/debossed effect.

- back of card - large, close-cropped, 'ghost' patterns of the C-shaped curves of logo, or company name repeated on back of card in spot UV.

Target Market(s)

- young to middle-aged professionals mainly (but ideally should design should suit all)

- UK, US,EU,AUS & ASIAN mainly (but ideally should design should suit all countries)

Industry/Entity Type

Real Estate

Requirements
Must have
• THEME:
- Luxurious & Modern
- Clean & striking
- Unique & creative

INFO:
- Logo & company name on front
- Contact details on back:

Tobias Hennlund
Managing Director

www.velmontestates.asia
www.velmontestates.co.uk

Tel: 083-274-6159
email: tobias@velmontestates.asia

(contact details can be displayed in any order as suites design.)

Nice to have
• - curved corner(s) to the card, white on front & turquoise on back or visa versa.

Should not have
• - No generic images of properties, palm trees/coconut trees etc.

- No other other bold colors, except for main turquoise, grey, metallic white & black theme.

- No obvious business card templates

```html
<!DOCTYPE html>
<html lang="en">
<head>
<meta charset="utf-8">
<title>Velmont Estates – Business Card</title>
<link rel="stylesheet" href="https://fonts.googleapis.com/css2?family=Marcellus&display=swap">
<style>
  :root {
    --turquoise: #52fbb7;
    --turquoise-ghost: #b8f3ff;
    --graphite: #5f666b;
    --ghost-grey: #d4d6d7;
    --card-white: #ffffff;
    --backdrop-light: #c9cdcd;
    --backdrop-dark: #8f9596;
  }
  * { box-sizing: border-box; margin: 0; padding: 0; }
  html, body { width: 1200px; height: 900px; overflow: hidden; }
  body {
    background: radial-gradient(ellipse at 50% 55%, var(--backdrop-light) 0%, var(--backdrop-dark) 100%);
    font-family: "Marcellus", "Optima", sans-serif;
    display: flex;
    flex-direction: column;
    align-items: center;
    justify-content: center;
    gap: 56px;
  }
  .card {
    width: 600px;
    height: 343px;
    background: var(--card-white);
    border-radius: 14px;
    position: relative;
    overflow: hidden;
    box-shadow: 0 8px 24px rgba(0, 0, 0, 0.18);
  }

  /* Front */
  .card-front {
    display: flex;
    align-items: center;
    justify-content: center;
    gap: 26px;
  }
  .brand-square {
    width: 112px;
    height: 112px;
    background: var(--turquoise);
  }
  .brand-name {
    color: var(--graphite);
    font-size: 50px;
    line-height: 1;
    letter-spacing: 0.5px;
  }

  /* Back */
  .name-band {
    position: absolute;
    top: 0; left: 0; right: 0;
    height: 165px;
    background: var(--turquoise);
  }
  .band-ghost {
    position: absolute;
    top: 0;
    height: 165px;
    width: 90px;
    background: linear-gradient(90deg, rgba(184, 243, 255, 0.55), rgba(184, 243, 255, 0));
  }
  .band-ghost.left { left: 0; }
  .band-ghost.right { right: 0; transform: scaleX(-1); }
  .holder {
    position: absolute;
    left: 160px;
    top: 50px;
    color: var(--card-white);
  }
  .holder-name { font-size: 36px; line-height: 1.1; }
  .holder-title { font-size: 24px; letter-spacing: 1px; margin-top: 10px; }

  .contact {
    position: absolute;
    left: 30px;
    top: 200px;
    color: var(--graphite);
    font-size: 16px;
    line-height: 1.3;
    list-style: none;
  }
  .contact .web { margin-top: 10px; }
  .contact .web + .web { margin-top: 0; }

  .corner-ghost {
    position: absolute;
    right: 18px;
    bottom: 0;
    width: 170px;
    height: 160px;
    background: linear-gradient(135deg, rgba(212, 214, 215, 0.9), rgba(212, 214, 215, 0.35));
    border-radius: 8px 8px 0 0;
  }
</style>
</head>
<body>

  <section class="card card-front" aria-label="Card front">
    <div class="brand-square"></div>
    <h1 class="brand-name">Velmont Estates</h1>
  </section>

  <section class="card card-back" aria-label="Card back">
    <div class="name-band">
      <div class="band-ghost left" role="img" aria-label="Faint ghost pattern of brand curves"></div>
      <div class="band-ghost right" role="img" aria-label="Faint ghost pattern of brand curves"></div>
      <div class="holder">
        <h2 class="holder-name">Tobias Hennlund</h2>
        <p class="holder-title">MANAGING DIRECTOR</p>
      </div>
    </div>

    <ul class="contact">
      <li>Tel: 083-274-6159</li>
      <li>email: tobias@velmontestates.asia</li>
      <li class="web">www.velmontestates.asia</li>
      <li class="web">www.velmontestates.co.uk</li>
    </ul>

    <div class="corner-ghost" role="img" aria-label="Large grey ghost pattern of brand curves"></div>
  </section>

</body>
</html>
```